NEW Modern Sleek Business Card for VR Language Startup

Our startup is using VR to lead the next wave of world language education. We need a two-sided business card that introduces the larger organization (Brightloom Language Inc) and our contact info on one side and shows the product, Glimwoorld, on the other side.

Side 1 (contact info)= Brightloom Logo and Contact info (name, title, phone, email)

Side 2 (product)= Glimworld logo, text, and website
Text= Culturally Immersive Language Learning Games
Website= www.glimworld-play.com

Target Market(s)

Education, Technology

Contact Information for Business Card

Contact info will be updated upon approval of the design. For now, put this as a placeholder.

Perry Dunmore
Founder & CEO
pdunmore@quillpost-mail.net
(555)-014-2286

Font styles to use
Other font styles liked:
• Gibson and Century Gothic are the brand fonts

Requirements
Nice to have
• I would love to see cohesion between the design and colors of the two logos. I have attached a few business card designs that I like, so you can get a feel for my preferred style.

```html
<!DOCTYPE html>
<html lang="en">
<head>
<meta charset="utf-8">
<title>Brightloom Language – Business Card</title>
<link rel="stylesheet" href="https://fonts.googleapis.com/css2?family=Lato:wght@400;700&display=swap">
<style>
  :root {
    --backdrop: #e4e4e6;
    --card-dark: #4a4a4c;
    --card-light: #ffffff;
    --ink: #1c1c1e;
    --ink-soft: #3a3a3c;
    --white: #ffffff;
    --link-blue: #2fb4f0;
    --name-violet: #6b5cf0;
    --cool-a: #22e0ee;
    --cool-b: #35b0f4;
    --cool-c: #5c6cf8;
    --warm-a: #f7a23a;
    --warm-b: #f4304a;
    --warm-c: #a23bd8;
    --warm-d: #5a6af8;
    --warm-e: #1ce0e6;
  }
  * { box-sizing: border-box; margin: 0; padding: 0; }
  html, body {
    width: 1200px; height: 900px; overflow: hidden;
    background: var(--backdrop);
    font-family: "Lato", Arial, sans-serif;
  }
  .canvas { position: relative; width: 1200px; height: 900px; }

  .card {
    position: absolute;
    width: 560px; height: 320px;
    border-radius: 22px;
    overflow: hidden;
    box-shadow: 0 14px 30px rgba(0,0,0,0.18);
  }
  .card--product { left: 90px; top: 90px; background: var(--card-dark); }
  .card--contact { left: 550px; top: 490px; background: var(--card-light); }

  .brand-art { position: absolute; right: 0; top: 0; width: 300px; height: 320px; }
  .card--product .brand-art {
    background: linear-gradient(160deg, var(--cool-a), var(--cool-b) 55%, var(--cool-c));
    border-radius: 0 0 0 300px;
  }
  .card--contact .brand-art {
    background: linear-gradient(150deg, var(--warm-a), var(--warm-b) 35%, var(--warm-c) 60%, var(--warm-d) 80%, var(--warm-e));
    border-radius: 0 0 0 300px;
  }

  .content { position: absolute; left: 40px; }

  .wordmark { display: flex; align-items: center; gap: 12px; font-weight: 700; }
  .wordmark__dot { width: 18px; height: 18px; border-radius: 50%; }
  .card--product .wordmark { color: var(--white); font-size: 34px; }
  .card--product .wordmark__dot { background: var(--cool-b); }
  .card--contact .wordmark { color: var(--ink); font-size: 34px; letter-spacing: 1px; }
  .card--contact .wordmark__dot { background: var(--warm-b); }

  .card--product .content { top: 100px; }
  .tagline {
    margin-top: 28px;
    color: var(--white);
    font-size: 15px; letter-spacing: 1px; line-height: 1.35;
    text-transform: uppercase;
  }
  .website { margin-top: 18px; color: var(--link-blue); font-size: 17px; letter-spacing: 0.5px; }

  .card--contact .content { top: 60px; }
  .person { margin-top: 38px; }
  .person__name { color: var(--name-violet); font-size: 21px; text-transform: uppercase; letter-spacing: 0.5px; }
  .person__title { color: var(--ink); font-size: 16px; margin-top: 2px; }
  .details { margin-top: 18px; list-style: none; }
  .details li { display: flex; align-items: center; gap: 8px; color: var(--ink-soft); font-size: 16px; line-height: 1.6; }
  .details svg { width: 15px; height: 15px; flex: none; }
</style>
</head>
<body>
<main class="canvas">

  <section class="card card--product" aria-label="Product side">
    <div class="brand-art" role="img" aria-label="Large brand graphic in cyan-to-blue gradient"></div>
    <div class="content">
      <div class="wordmark"><span class="wordmark__dot"></span>Glimworld</div>
      <p class="tagline">Culturally Immersive<br>Language Learning Games</p>
      <p class="website">www.glimworld-play.com</p>
    </div>
  </section>

  <section class="card card--contact" aria-label="Contact side">
    <div class="brand-art" role="img" aria-label="Large brand graphic in orange, red, violet and cyan gradient"></div>
    <div class="content">
      <div class="wordmark"><span class="wordmark__dot"></span>Brightloom</div>
      <div class="person">
        <p class="person__name">Perry Dunmore</p>
        <p class="person__title">Founder &amp; CEO</p>
      </div>
      <ul class="details">
        <li>
          <svg viewBox="0 0 16 16" aria-hidden="true"><path fill="#f4504a" d="M3 1l3 3-1.5 2a9 9 0 0 0 5.5 5.5L12 10l3 3-2 2C7 15 1 9 1 3z"/></svg>
          (555)-014-2286
        </li>
        <li>
          <svg viewBox="0 0 16 16" aria-hidden="true"><rect x="1" y="3" width="14" height="10" rx="1.5" fill="#6b5cf0"/><path d="M1.5 4l6.5 5 6.5-5" fill="none" stroke="#fff" stroke-width="1.3"/></svg>
          pdunmore@quillpost-mail.net
        </li>
      </ul>
    </div>
  </section>

</main>
</body>
</html>
```